IT consulting company looking for a modern business design for a website and a new logo

We are the IT-consulting company VelmaTrix from Germany and need a new and modern business website and a new logo. We are specialized in output management. Our services include business analysis, outsourcing, development, training and project leading. We wish for a design with nature pictures (mountains, lakes, rivers, forests, etc.) for our company with the colors green and blue. If it is possible, a slow-mo video of a nature scene. The design should be responsive and the menu should change to a hamburger menu. The following are: • Services / Solutions 1. Output Management 2. Outsourcing 3. Development 4. Business Analyst 5. Training • Partners • Careers • About Us 1. Project A 2. Project B 3. Project C • Contact Notes for the following categories: For "Services / Solutions" we want to conclude some contents from all the sub-points and sub-points below. Additionally, we would like to see some sub-point under "Services / Solutions". For Output Management: "5 Benefits of Output Management Systems (OMS) - OMS Simplifies and Accelerates External Communication - Helps Reduce Communication Mistakes - Provides Customers With Fast and Secure Responses to your questions - Employees can focus on the essential as they can access prepared templates - Companies get complete transparency about their communication "The point" partner does not have sub-points. The content here is a quote and the logo from the company Brel. For now, just placeholders on this site. The next point wants to be "career" without sub-point and wants to contain some text. Carrer options wants to be listed here. Next point wants to be "About us", where we need sub-points which we do not know exactly at this moment, but they will contain text. By clicking directly on "About us" we want to include pictures and texts about 6 employees for which we only need placeholders at the moment. The last point wants to be "contact", where customers can send us messages. The main page should include a story about our company, which can be a placeholder for now. For reference, designs have a look at: https://brelvanto.de/ https://www.tarnopix.com/ https://www.pldrive.de/ We prefer WordPress designs, created with the plugin ELEMENTOR, so that we can easily edit the content by ourselves. The final design should look professional, competent and modern.

Target Market(s)

With our website, we want to reach the following target groups. <br> <br> <br> <br> <br> <br> <br> <br> <br> <br> <br> <br> <br> <br> <br> <br> <br> <br> <br> <br> <br> <br> <br> <br> <br> <br> <br> <br> <br> <br> <br> <br> <br> <br> <br> <br> <br> <br> <br> <br> <br> <br> <br> <br> <br> <br> <br> <br> <br>

Industry/Entity Type

Consulting

Logo Text

(optionally) VelmaTrix

Font styles to use
Sans Serif

Colors

Designer to choose colors to be used in the design.

Requirements
Must have
• 1. Outsourcing 3. Development 4. Business Analyst 5. Training • Partners • Careers • About Us 1. Project A 2. Project B 3. Project C • Contact The above-mentioned background picture with nature motifs (mountains, lakes, rivers, forests, etc.). WordPress design in primary colors blue and green.
Nice to have
• ELEMENTOR template. Effects for the background pictures. Counter of all successful projects for Output Management, Business Analyst and Training

```html
<!DOCTYPE html>
<html lang="en">
<head>
<meta charset="utf-8">
<title>VelmaTrix – IT Consulting</title>
<link rel="stylesheet" href="https://fonts.googleapis.com/css2?family=Ubuntu:wght@500;700&family=Roboto:wght@400;500;700&display=swap">
<style>
:root{
  --blue:#0d4fa3;
  --blue-dark:#0a3f86;
  --green:#5aab2e;
  --green-light:#6cbb3c;
  --ink:#1f1f1f;
  --text:#6b6b6b;
  --white:#ffffff;
  --line:#dcdcdc;
}
*{margin:0;padding:0;box-sizing:border-box}
html,body{width:1200px;height:4525px;overflow:hidden}
body{position:relative;background:#f7f8f8;font-family:"Roboto",sans-serif;color:var(--text)}
.abs{position:absolute}
h1,h2,.logo{font-family:"Ubuntu",sans-serif;color:var(--ink)}

/* hero */
.hero{left:0;top:0;width:1200px;height:800px;overflow:hidden}
.hero-photo{position:absolute;inset:0;background:linear-gradient(180deg,#6f8796 0%,#a9b9c2 18%,#5d7a67 38%,#3d6a4a 52%,#2aa0b8 66%,#3b7c3a 82%,#5a8f36 100%)}
.hero-wave{position:absolute;left:0;top:0}
.logo{color:var(--white);font-size:38px;font-weight:700;left:111px;top:44px;letter-spacing:.2px}
.nav{top:55px;right:111px;display:flex;gap:30px}
.nav a{color:var(--white);font-family:"Roboto",sans-serif;font-weight:700;font-size:16px;text-decoration:none}
.hero-title{left:0;width:1200px;top:222px;text-align:center;color:var(--white);font-size:60px;font-weight:700}
.hero-sub{left:0;width:1200px;top:308px;text-align:center;color:var(--white);font-weight:700;font-size:18.5px;line-height:34px}
.btn{display:flex;align-items:center;justify-content:center;gap:6px;background:var(--green);color:var(--white);font-weight:700;font-size:15px;border-radius:26px;text-decoration:none}
.btn .arr{width:14px;height:14px}
.hero-btn{left:503px;top:398px;width:194px;height:49px}

/* about */
.about-bg{left:0;top:800px;width:1200px;height:1340px;background:linear-gradient(180deg,#ffffff 0%,#f0f2f2 45%,#eceeee 70%,#f6f7f7 100%)}
.about-title{left:111px;top:862px;font-size:46px;font-weight:700}
.about-text{left:111px;top:955px;width:490px;font-size:14.5px;line-height:28px;color:var(--text)}
.about-text p+p{margin-top:28px}
.about-btn{left:111px;top:1229px;width:198px;height:49px}
.about-visual{left:650px;top:850px}

.divider{left:111px;top:1409px;width:978px;height:1px;background:var(--line)}

/* services */
.section-title{left:0;width:1200px;text-align:center;font-size:46px;font-weight:500}
.section-lead{left:0;width:1200px;text-align:center;font-size:14.5px;line-height:27px;color:var(--text)}
.svc{width:270px;height:270px;border-radius:50%;color:var(--white);text-align:center}
.svc-blue{background:radial-gradient(circle at 45% 40%,#1a63bd,var(--blue) 70%)}
.svc-green{background:radial-gradient(circle at 45% 40%,#72c045,var(--green) 70%)}
.svc-ring{width:314px;height:314px;border-radius:50%;border:3px solid var(--green)}
.svc svg{position:absolute;left:105px;top:36px}
.svc h3{position:absolute;top:133px;width:100%;font-family:"Roboto",sans-serif;font-weight:500;font-size:22px}
.svc p{position:absolute;top:173px;left:30px;right:30px;font-size:13.5px;line-height:26px}

/* team */
.team-band{left:0;top:2137px;width:1200px;height:332px;background:linear-gradient(90deg,#5aa92f,#63b03a 50%,#5aa92f)}
.team-title{color:var(--white)}
.member-photo{width:290px;height:200px}
.role{height:35px;background:var(--blue);color:var(--white);font-weight:500;font-size:19px;line-height:35px;padding-left:24px;width:185px}
.member-name{font-family:"Roboto",sans-serif;font-weight:500;font-size:22px;color:#2a2a2a;letter-spacing:.2px}
.member-text{width:290px;font-size:13.5px;line-height:26px;text-align:justify;color:var(--text)}
.social{display:flex;gap:12px}
.social span{width:12px;height:12px;border-radius:50%;background:var(--green)}

/* partners */
.partners-bg{left:0;top:3277px;width:1200px;height:700px;background:linear-gradient(180deg,#f2f3f3 0%,#f6f7f7 60%,#ffffff 100%)}
.partner{width:183px;height:93px;background:var(--white);border:1px solid #e6e6e6;display:flex;align-items:center;justify-content:center;font-family:"Roboto",sans-serif;font-weight:700;font-size:17px;color:#2b3a55;text-align:center;padding:0 10px}

/* footer */
.footer-wave{left:0;top:3860px}
.footer-bg{left:0;top:4110px;width:1200px;height:415px;background:var(--blue)}
.f-head{color:var(--white);font-weight:500;font-size:15px;letter-spacing:.3px}
.f-list{list-style:none;color:var(--white);font-size:13.5px}
.f-list li{height:29px;display:flex;align-items:center;gap:10px}
.f-list li::before{content:"»";font-size:14px}
.f-contact{color:var(--white);font-size:13.5px;line-height:22px}
.f-contact .row{display:flex;gap:14px;position:absolute;left:0;width:260px}
.f-contact svg{flex:none;margin-top:2px}
.f-text{color:var(--white);font-size:13.5px;line-height:22px;width:270px}
.f-input{width:266px;height:33px;border:1px solid rgba(255,255,255,.7);color:var(--white);font-size:12px;line-height:31px;padding-left:12px}
.f-sub{width:107px;height:33px;font-size:12px;border-radius:20px}
.f-rule{top:4428px;height:1px;background:rgba(255,255,255,.6)}
.f-social{left:512px;top:4410px;display:flex;gap:12px}
.f-social span{width:36px;height:36px;border-radius:50%;border:2px solid var(--white)}
.copy{left:0;width:1200px;top:4472px;text-align:center;color:var(--white);font-size:14px}
</style>
</head>
<body>

<!-- hero -->
<section class="abs hero">
  <div class="hero-photo" role="img" aria-label="Nature photograph: mountain valley with a turquoise lake, forests and green meadows"></div>
  <svg class="hero-wave" width="1200" height="800" viewBox="0 0 1200 800" aria-hidden="true">
    <path d="M0,620 C110,700 230,760 420,748 C700,728 920,600 1200,612 L1200,800 L0,800Z" fill="#f7f8f8"/>
    <path d="M240,748 C520,752 820,590 1200,600 L1200,632 C840,620 580,790 280,762Z" fill="#0d4fa3"/>
    <path d="M560,748 C820,660 1040,650 1200,720 L1200,782 C1060,700 840,690 560,758Z" fill="#5aab2e"/>
  </svg>
  <div class="abs logo">VelmaTrix</div>
  <nav class="abs nav"><a href="#">HOME</a><a href="#">ABOUT US</a><a href="#">SERVICES</a><a href="#">PARTNER</a><a href="#">CAREERS</a><a href="#">CONTACT</a></nav>
  <h1 class="abs hero-title">VelmaTrix</h1>
  <p class="abs hero-sub">Lorem ipsum dolor sit amet consectetur adipiscing elit sed do labore et eiusmod<br>tempor incididunt ut labore et dolore magna aliqua.</p>
  <a class="abs btn hero-btn" href="#">READ MORE <svg class="arr" viewBox="0 0 14 14"><circle cx="7" cy="7" r="7" fill="#fff"/><path d="M5 4l3.5 3L5 10" stroke="#5aab2e" stroke-width="2" fill="none"/></svg></a>
</section>

<!-- about -->
<div class="abs about-bg"></div>
<h2 class="abs about-title">About VelmaTrix</h2>
<div class="abs about-text">
  <p>Lorem ipsum dolor sit amet, consectetur adipiscing elit, sed do eiusmod tempor incididunt ut labore et dolore magna aliqua.</p>
  <p>Ut enim ad minim veniam, quis nostrud exercitation ullamco laboris nisi ut aliquip ex ea commodo consequat. Duis aute irure dolor in reprehen derit in voluptate velit esse cillum dolore eu fugiat nulla pariatur. Excep teur sint oc caecat cupidatat non proident, sunt in culpa qui officia dese runt mollit anim id est laborum.</p>
</div>
<a class="abs btn about-btn" href="#">READ MORE <svg class="arr" viewBox="0 0 14 14"><circle cx="7" cy="7" r="7" fill="#fff"/><path d="M5 4l3.5 3L5 10" stroke="#5aab2e" stroke-width="2" fill="none"/></svg></a>
<svg class="abs about-visual" width="440" height="440" viewBox="0 0 440 440">
  <circle cx="234" cy="230" r="210" fill="#0d4fa3"/>
  <circle cx="221" cy="216" r="208" fill="#ffffff"/>
  <circle cx="221" cy="216" r="200" fill="#a9b4bc" role="img" aria-label="Photograph of a consultant in a meeting at a laptop"/>
</svg>
<div class="abs divider"></div>

<!-- services -->
<h2 class="abs section-title" style="top:1510px">Our Services</h2>
<p class="abs section-lead" style="top:1594px">Lorem ipsum dolor sit amet, consectetur adipiscing elit do eiusmod tempor incididunt ut labore et dolore magna<br>aliqua. Ut enim ad minim veniam, quis nostrud exercitation ullamco laboris nisi.</p>

<div class="abs svc svc-blue" style="left:116px;top:1713px">
  <svg width="60" height="70" viewBox="0 0 60 70" fill="none" stroke="#fff" stroke-width="2.4"><circle cx="30" cy="30" r="8"/><path d="M18 46c2-8 22-8 24 0M30 4v10M30 56v10M4 30h10M46 30h10"/></svg>
  <h3>OUTSOURCING</h3><p>Lorem ipsum dolor sit ametmet consectetur adipiscing.</p>
</div>
<div class="abs svc-ring" style="left:442px;top:1691px"></div>
<div class="abs svc svc-green" style="left:464px;top:1713px">
  <svg width="60" height="70" viewBox="0 0 60 70" fill="none" stroke="#fff" stroke-width="2.4"><circle cx="30" cy="32" r="22"/><circle cx="30" cy="32" r="12"/><circle cx="30" cy="32" r="5"/></svg>
  <h3>DEVELOPMENT</h3><p>Lorem ipsum dolor sit ametmet consectetur adipiscing.</p>
</div>
<div class="abs svc svc-blue" style="left:812px;top:1713px">
  <svg width="60" height="70" viewBox="0 0 60 70" fill="none" stroke="#fff" stroke-width="2.4"><rect x="6" y="6" width="34" height="26"/><circle cx="44" cy="40" r="6"/><path d="M32 64V54h24v10M6 64h50"/></svg>
  <h3>TRAININGS</h3><p>Lorem ipsum dolor sit ametmet consectetur adipiscing.</p>
</div>

<!-- team -->
<div class="abs team-band"></div>
<h2 class="abs section-title team-title" style="top:2236px">Our Team</h2>

<div class="abs member-photo" style="left:123px;top:2356px;background:linear-gradient(160deg,#d7dde2,#8f9aa4)" role="img" aria-label="Portrait photograph of the founder"></div>
<div class="abs role" style="left:111px;top:2495px">THE FUNDER</div>
<div class="abs member-name" style="left:121px;top:2588px">ARVID KESLER</div>
<p class="abs member-text" style="left:123px;top:2628px">Lorem ipsum dolor sit amet, consectetur ad ipiscing elit, sed do eiusmod tempor incidi dunt ut labore et dolore.</p>
<div class="abs social" style="left:123px;top:2727px"><span></span><span></span><span></span></div>

<div class="abs member-photo" style="left:460px;top:2356px;background:linear-gradient(160deg,#c9925e,#8d6a4e)" role="img" aria-label="Portrait photograph of the chairwoman"></div>
<div class="abs role" style="left:450px;top:2495px">CHERMAN</div>
<div class="abs member-name" style="left:460px;top:2588px">LINNEA MARSH</div>
<p class="abs member-text" style="left:460px;top:2628px">Lorem ipsum dolor sit amet, consectetur ad ipiscing elit, sed do eiusmod tempor incidi dunt ut labore et dolore.</p>
<div class="abs social" style="left:460px;top:2727px"><span></span><span></span><span></span></div>

<div class="abs member-photo" style="left:798px;top:2356px;background:linear-gradient(160deg,#8a6a58,#3f3c44)" role="img" aria-label="Portrait photograph of the assistant manager"></div>
<div class="abs role" style="left:788px;top:2495px">AS.MANAGER</div>
<div class="abs member-name" style="left:798px;top:2588px">TOMAS REYL</div>
<p class="abs member-text" style="left:798px;top:2628px">Lorem ipsum dolor sit amet, consectetur ad ipiscing elit, sed do eiusmod tempor incidi dunt ut labore et dolore.</p>
<div class="abs social" style="left:798px;top:2727px"><span></span><span></span><span></span></div>

<div class="abs member-photo" style="left:121px;top:2783px;background:linear-gradient(160deg,#e2e4e2,#a8aba6)" role="img" aria-label="Portrait photograph of the co-manager"></div>
<div class="abs role" style="left:110px;top:2922px">CO-MANAGER</div>
<div class="abs member-name" style="left:120px;top:3015px">INES CALDER</div>
<p class="abs member-text" style="left:121px;top:3055px">Lorem ipsum dolor sit amet, consectetur ad ipiscing elit, sed do eiusmod tempor incidi dunt ut labore et dolore.</p>
<div class="abs social" style="left:121px;top:3154px"><span></span><span></span><span></span></div>

<div class="abs member-photo" style="left:459px;top:2783px;background:linear-gradient(160deg,#d6a77c,#6f7a52)" role="img" aria-label="Portrait photograph of the coordinator"></div>
<div class="abs role" style="left:449px;top:2922px">CO-ORDINATOR</div>
<div class="abs member-name" style="left:458px;top:3015px">JONAS PREWITT</div>
<p class="abs member-text" style="left:459px;top:3055px">Lorem ipsum dolor sit amet, consectetur ad ipiscing elit, sed do eiusmod tempor incidi dunt ut labore et dolore.</p>
<div class="abs social" style="left:459px;top:3154px"><span></span><span></span><span></span></div>

<div class="abs member-photo" style="left:797px;top:2783px;background:linear-gradient(160deg,#c5cdd4,#51708f)" role="img" aria-label="Portrait photograph of the manager"></div>
<div class="abs role" style="left:786px;top:2922px">MANAGER</div>
<div class="abs member-name" style="left:796px;top:3015px">MIRA VANTHOLT</div>
<p class="abs member-text" style="left:797px;top:3055px">Lorem ipsum dolor sit amet, consectetur ad ipiscing elit, sed do eiusmod tempor incidi dunt ut labore et dolore.</p>
<div class="abs social" style="left:797px;top:3154px"><span></span><span></span><span></span></div>

<!-- partners -->
<div class="abs partners-bg"></div>
<h2 class="abs section-title" style="top:3383px">Our Partners</h2>
<p class="abs section-lead" style="top:3466px">Lorem ipsum dolor sit amet, consectetur adipiscing elit, sed do eiusmod tempor incididunt ut labore et dolore<br>magna aliqua. Ut enim ad minim veniam, quis nostrud exercitation ullamco laboris nisi.</p>

<div class="abs partner" style="left:111px;top:3558px">Norveld</div>
<div class="abs partner" style="left:309px;top:3558px">Halvane</div>
<div class="abs partner" style="left:508px;top:3558px;border-bottom:3px solid var(--green)">Banca Ostrellia</div>
<div class="abs partner" style="left:706px;top:3558px">Veltaris</div>
<div class="abs partner" style="left:905px;top:3558px">Krona Bank</div>

<div class="abs partner" style="left:111px;top:3665px">Meridale Life</div>
<div class="abs partner" style="left:309px;top:3665px">Tavisson Financial</div>
<div class="abs partner" style="left:508px;top:3665px">Postbright</div>
<div class="abs partner" style="left:706px;top:3665px">Société Arlenne</div>
<div class="abs partner" style="left:905px;top:3665px">Quanhai Bank</div>

<div class="abs partner" style="left:111px;top:3772px">Solvane Trust</div>
<div class="abs partner" style="left:309px;top:3772px">Brekker Audit</div>
<div class="abs partner" style="left:508px;top:3772px">Swiftcarry</div>
<div class="abs partner" style="left:706px;top:3772px">Lumora</div>
<div class="abs partner" style="left:905px;top:3772px">Cresta Money</div>

<!-- footer -->
<svg class="abs footer-wave" width="1200" height="260" viewBox="0 0 1200 260" aria-hidden="true">
  <path d="M0,250 C220,210 420,205 640,185 C880,160 1060,110 1200,20 L1200,260 L0,260Z" fill="#0d4fa3"/>
  <path d="M0,215 C240,200 470,200 700,170 C940,140 1080,80 1200,15 L1200,40 C1080,110 930,170 700,195 C470,220 240,222 0,232Z" fill="#5aab2e"/>
  <path d="M260,200 C520,195 780,190 980,130 C1080,100 1150,60 1200,30 L1200,50 C1140,90 1080,125 990,150 C780,205 520,214 260,212Z" fill="#ffffff"/>
</svg>
<div class="abs footer-bg"></div>

<div class="abs f-head" style="left:111px;top:4190px">QUICK LINKS</div>
<ul class="abs f-list" style="left:111px;top:4227px"><li>Home</li><li>About Us</li><li>Services</li><li>Partners</li><li>Location</li></ul>

<div class="abs f-head" style="left:297px;top:4190px">OTHER LINKS</div>
<ul class="abs f-list" style="left:297px;top:4227px"><li>Reviews</li><li>Help</li><li>Terms &amp; Conditions</li><li>FAQs</li><li>Contact Us</li></ul>

<div class="abs f-head" style="left:525px;top:4190px">CONTACT US</div>
<div class="abs f-contact" style="left:525px;top:4232px;width:270px;height:120px">
  <div class="row" style="top:0"><svg width="12" height="16" viewBox="0 0 12 16"><path d="M6 0a6 6 0 0 0-6 6c0 4.5 6 10 6 10s6-5.5 6-10a6 6 0 0 0-6-6z" fill="#fff"/><circle cx="6" cy="6" r="2.2" fill="#0d4fa3"/></svg><span>48 Lindenweg, Aldersfeld<br>New State 4102.</span></div>
  <div class="row" style="top:66px"><svg width="14" height="14" viewBox="0 0 14 14"><path d="M3 0l3 3-2 2c1 2 3 4 5 5l2-2 3 3-2 3C6 14 0 8 0 2z" fill="#fff"/></svg><span>(+1) 555 204 3187</span></div>
  <div class="row" style="top:108px"><svg width="14" height="11" viewBox="0 0 14 11"><rect width="14" height="11" fill="#fff"/><path d="M0 0l7 6 7-6" stroke="#0d4fa3" stroke-width="1.5" fill="none"/></svg><span>info@velmatrix.com</span></div>
</div>

<div class="abs f-head" style="left:822px;top:4190px">NEWSLETTER SUBSCRIPTION</div>
<p class="abs f-text" style="left:822px;top:4227px">Register your Email Address to get more Information about us</p>
<div class="abs f-input" style="left:822px;top:4280px">Email Address</div>
<a class="abs btn f-sub" style="left:822px;top:4337px" href="#">SUBSCRIBE</a>

<div class="abs f-rule" style="left:111px;width:385px"></div>
<div class="abs f-rule" style="left:704px;width:385px"></div>
<div class="abs f-social"><span></span><span></span><span></span><span></span></div>
<p class="abs copy">Copyrights © 2019 VelmaTrix.&nbsp; All Rights Reserved &nbsp;&nbsp; | &nbsp;&nbsp; Privacy Policy.</p>

</body>
</html>
```